Professional, modern and unique business card. We are looking to present a new look to our business cards however we don't want to divert too far away from original template. We want social media links and our 3 office addresses on the backside of the business cards. Please see attached business card templates for ideas.
Crestline Homes Color Code:
R: 7
G:63
B:86

Target Market(s)

Real Estate

Industry/Entity Type

Real Estate

Contact Information for Business Card

Follow the attached templates. In need of a more modern and unique touch but don't want to divert from the original theme or color.
Crestline Homes Color Code:
R: 7
G:63
B:86

Font styles to use
Serif

Requirements
Must have
• Crestline Homes logo, Crestline homes colors, social media links, 3 office addresses,
Nice to have
• information about Crestline Homes and QR codes. You can check out www.mycrestlinehomes.example

```html
<!DOCTYPE html>
<html lang="en">
<head>
<meta charset="utf-8">
<title>Crestline Homes – Business Card</title>
<link href="https://fonts.googleapis.com/css2?family=Lato:wght@300;400;700&display=swap" rel="stylesheet">
<style>
  :root {
    --stage: #a9a9a9;
    --brand: #073f56;
    --brand-ink: #ffffff;
    --brand-soft: #cfe0ea;
    --logo-tint: #dfeef5;
    --paper: #ffffff;
    --paper-arc: #eef0f2;
    --ink: #1c1c1c;
  }
  * { box-sizing: border-box; margin: 0; padding: 0; }
  html, body { width: 1200px; height: 900px; overflow: hidden; }
  body {
    background: var(--stage);
    font-family: "Lato", sans-serif;
    position: relative;
  }
  .card {
    position: absolute;
    top: 200px;
    width: 310px;
    height: 502px;
    overflow: hidden;
  }
  .card--front {
    left: 253px;
    background: var(--brand);
    color: var(--brand-ink);
    border-radius: 62px 0 62px 0;
  }
  .card--back {
    left: 627px;
    background: var(--paper);
    color: var(--ink);
    border-radius: 0 62px 0 62px;
  }

  /* Front */
  .wordmark {
    position: absolute;
    top: 128px;
    left: 0;
    width: 100%;
    text-align: center;
    color: var(--logo-tint);
    font-weight: 700;
  }
  .wordmark__main { display: block; font-size: 36px; letter-spacing: 1px; line-height: 1; }
  .wordmark__sub { display: block; font-size: 15px; letter-spacing: 12px; margin-top: 14px; padding-left: 12px; line-height: 1; }

  .person { position: absolute; left: 32px; top: 318px; }
  .person__name { font-size: 21px; font-weight: 700; letter-spacing: 0.3px; line-height: 1; }
  .person__title { font-size: 14px; font-weight: 300; color: var(--brand-soft); letter-spacing: 0.4px; margin-top: 6px; line-height: 1; }

  .contacts { position: absolute; left: 33px; top: 376px; list-style: none; }
  .contacts li { display: flex; align-items: center; font-size: 14px; height: 17px; line-height: 17px; }
  .contacts svg { width: 12px; height: 12px; margin-right: 5px; fill: var(--brand-ink); flex: none; }

  /* Back */
  .arcs { position: absolute; inset: 0; }
  .social { position: absolute; left: 41px; top: 124px; list-style: none; }
  .social li { display: flex; align-items: center; font-size: 15px; }
  .social li + li { margin-top: 8px; }
  .social__dot { width: 22px; height: 22px; border-radius: 50%; background: var(--brand); margin-right: 6px; flex: none; }

  .offices { position: absolute; left: 42px; top: 336px; font-style: normal; }
  .office { font-size: 14.5px; line-height: 17px; }
  .office + .office { margin-top: 11px; }
</style>
</head>
<body>

  <section class="card card--front" aria-label="Business card front">
    <div class="wordmark">
      <span class="wordmark__main">CRESTLINE</span>
      <span class="wordmark__sub">HOMES</span>
    </div>

    <div class="person">
      <p class="person__name">DANA WHITFIELD</p>
      <p class="person__title">MANAGING DIRECTOR</p>
    </div>

    <ul class="contacts">
      <li><svg viewBox="0 0 12 12"><path d="M1 4c0-2 2-3 5-3s5 1 5 3l-2 1-1-1.5H4L3 5zM3 6h6l1 5H2z"/></svg>444 555 0186</li>
      <li><svg viewBox="0 0 12 12"><path d="M3 0h6v12H3zM4 1.5v8h4v-8z"/></svg>888 555 0143</li>
      <li><svg viewBox="0 0 12 12"><path d="M3 0h6v3H3zM1 4h10v5H9v3H3V9H1zM4 7v4h4V7z"/></svg>888 555 0100</li>
      <li><svg viewBox="0 0 12 12"><path d="M1 2.5h10v7H1zM1.5 3l4.5 3.5L10.5 3z" fill-rule="evenodd"/></svg>info@crestlinehomes.example</li>
      <li><svg viewBox="0 0 12 12"><circle cx="6" cy="6" r="5.5"/></svg>www.mycrestlinehomes.example</li>
    </ul>
  </section>

  <section class="card card--back" aria-label="Business card back">
    <svg class="arcs" viewBox="0 0 310 502" aria-hidden="true">
      <g fill="none" stroke="var(--paper-arc)" stroke-width="3">
        <circle cx="60" cy="330" r="230"/>
        <circle cx="60" cy="330" r="260"/>
        <circle cx="60" cy="330" r="290"/>
      </g>
    </svg>

    <ul class="social">
      <li><span class="social__dot"></span>CrestlineHomesNY</li>
      <li><span class="social__dot"></span>Info at Crestline Homes</li>
      <li><span class="social__dot"></span>Crestline Homes New York</li>
      <li><span class="social__dot"></span>Crestline Homes</li>
      <li><span class="social__dot"></span>@CrestlineHomesQ</li>
      <li><span class="social__dot"></span>@CrestlineHomesNY</li>
    </ul>

    <address class="offices">
      <p class="office">118-40 Harbor Blvd<br>Bayview, NY 11360</p>
      <p class="office">72-15 Linden Blvd<br>Elm Gardens, NY 11418</p>
      <p class="office">1450 Maple Ave<br>Brookside, NY 11210</p>
    </address>
  </section>

</body>
</html>
```